business card deign

Logo needs the following on it.
1. attached logo
2. Tagline - "If it keeps a drink cold or the party going...we do it!"
3. Name- Dalton Pikes, Founder and CPO
4. Address - 412 E. Carver Avenue, Ste 2207, Tampa, FL. 33917
5. Phone - 555.318.4726

```html
<!DOCTYPE html>
<html lang="en">
<head>
<meta charset="utf-8">
<title>Talvero Business Card</title>
<link href="https://fonts.googleapis.com/css2?family=Open+Sans:wght@400;600;700&family=Roboto:wght@500;700&display=swap" rel="stylesheet">
<style>
  :root {
    --page: #e7e1d8;
    --card-top: #d9d0c3;
    --card-edge: #efe9e0;
    --ink: #161514;
    --band: #161513;
    --band-glow: #2e2b27;
    --band-text: #d3c9bb;
    --warm-text: #b79f84;
    --art-tone: #0d0c0b;
  }
  * { margin: 0; padding: 0; box-sizing: border-box; }
  html, body { width: 1200px; height: 1046px; overflow: hidden; }
  body { background: var(--page); position: relative; font-family: "Open Sans", sans-serif; }

  .card {
    position: absolute; left: 100px; top: 250px; width: 1000px; height: 546px;
    background: var(--card-top); border-radius: 26px; overflow: hidden;
    border: 1px solid var(--card-edge);
    box-shadow: 0 18px 40px rgba(60, 45, 30, 0.18);
  }

  .person { position: absolute; right: 36px; top: 40px; text-align: right; }
  .person-name { font-family: "Roboto", sans-serif; font-weight: 700; font-size: 40px; line-height: 48px; color: var(--ink); letter-spacing: 0.2px; }
  .person-role { font-family: "Roboto", sans-serif; font-weight: 500; font-size: 23px; line-height: 30px; color: var(--ink); margin-top: 4px; }
  .person-bar { position: absolute; left: 975px; top: 43px; width: 24px; height: 72px; background: var(--ink); }

  .brand-art { position: absolute; left: 55px; top: 31px; width: 240px; height: 167px; }
  .brand-name {
    position: absolute; left: 37px; top: 210px;
    font-family: "Open Sans", sans-serif; font-weight: 700; font-size: 38px; line-height: 44px;
    letter-spacing: 20px; color: var(--ink);
  }

  .info-band {
    position: absolute; left: 0; top: 285px; width: 100%; height: 261px;
    background: radial-gradient(ellipse 380px 240px at 330px 110px, var(--band-glow), var(--band) 80%);
  }
  .tagline { position: absolute; left: 39px; top: 30px; font-size: 24px; line-height: 34px; font-weight: 600; color: var(--band-text); }
  .contact { position: absolute; left: 36px; top: 132px; list-style: none; }
  .contact li { display: flex; align-items: flex-start; font-size: 24px; line-height: 32px; color: var(--band-text); }
  .contact li + li { margin-top: 4px; }
  .contact .icon { width: 20px; height: 20px; margin: 6px 10px 0 0; flex: none; }
  .contact .address { color: var(--warm-text); }
</style>
</head>
<body>
  <section class="card">
    <svg class="brand-art" role="img" aria-label="Brand mark artwork area" viewBox="0 0 240 167">
      <rect width="240" height="167" rx="8" fill="var(--art-tone)" opacity="0.85"/>
    </svg>
    <div class="brand-name">TALVERO</div>

    <div class="person">
      <div class="person-name">Dalton Pikes</div>
      <div class="person-role">Founder and CPO</div>
    </div>
    <div class="person-bar"></div>

    <div class="info-band">
      <p class="tagline">If it keeps a drink cold or<br>the party going...we do it!</p>
      <ul class="contact">
        <li>
          <svg class="icon" viewBox="0 0 24 24" fill="var(--band-text)"><path d="M6.6 10.8a15.1 15.1 0 0 0 6.6 6.6l2.2-2.2c.3-.3.7-.4 1-.2 1.1.4 2.3.6 3.6.6.6 0 1 .4 1 1V20c0 .6-.4 1-1 1A17 17 0 0 1 3 4c0-.6.4-1 1-1h3.5c.6 0 1 .4 1 1 0 1.3.2 2.5.6 3.6.1.3 0 .7-.2 1z"/></svg>
          <span>555.318.4726</span>
        </li>
        <li>
          <svg class="icon" viewBox="0 0 24 24" fill="none" stroke="var(--warm-text)" stroke-width="2"><path d="M12 22s7-7.2 7-12.5A7 7 0 0 0 5 9.5C5 14.8 12 22 12 22z"/><circle cx="12" cy="9.5" r="2.5"/></svg>
          <span class="address">412 E. Carver Avenue,<br>Ste 2207, Tampa, FL. 33917</span>
        </li>
      </ul>
    </div>
  </section>
</body>
</html>
```